Brand Identity Stationary Package

Hello I'm looking for a full branding package for my Property Management Company. I have a logo but looking to have the following
Business Card
Email signature
Facebook cover photo
Letterhead (word.doc)
#10 Envelope
Pocket Folder - link to 9x12 pocket folder design specs https://www.printorbit-example.ca/marketing-materials/presentation-folders
would like everything to match and be brand identifiable. The company looks after residential properties/apartments and some commercial properties. Attached is a zip of the files.
For Business Card
Name: Gareth Lindqvist
Position: Operations Manager
Number: 1 (555) 384-2917
Email: Gareth@harborkey-example.ca
Website: Harborkey-example.ca
Property Management

```html
<!DOCTYPE html>
<html lang="en">
<head>
<meta charset="utf-8">
<title>Harborkey Business Cards</title>
<link href="https://fonts.googleapis.com/css2?family=Roboto:wght@400;500&family=Raleway:wght@600;700&display=swap" rel="stylesheet">
<style>
  :root {
    --backdrop: #d3d4d6;
    --card: #ffffff;
    --brand-green: #7cab3d;
    --ink: #444548;
    --logo-ink: #1c1c1c;
  }
  * { box-sizing: border-box; margin: 0; padding: 0; }
  html, body { width: 1200px; height: 1200px; overflow: hidden; }
  body { background: var(--backdrop); font-family: "Roboto", sans-serif; color: var(--ink); position: relative; }

  .card {
    position: absolute; left: 269px; width: 662px; height: 202px;
    background: var(--card);
    border-bottom: 13px solid var(--brand-green);
  }
  .card--one { top: 283px; }
  .card--two { top: 499px; }
  .card--three { top: 715px; }

  .identity { position: absolute; left: 46px; top: 30px; }
  .identity__name { font-family: "Raleway", sans-serif; font-weight: 700; font-size: 21px; color: var(--brand-green); letter-spacing: 0.2px; line-height: 1.2; }
  .identity__title { font-size: 17.5px; line-height: 1.25; }

  .wordmark {
    position: absolute; right: 46px;
    font-family: "Raleway", sans-serif; font-weight: 700; font-size: 29px;
    letter-spacing: 2.5px; color: var(--logo-ink); line-height: 1;
  }
  .card--one .wordmark, .card--two .wordmark { top: 34px; }
  .card--three .wordmark { top: 76px; }

  .contacts { position: absolute; list-style: none; font-size: 17.5px; line-height: 22.5px; }
  .contacts li { display: flex; align-items: center; gap: 7px; white-space: nowrap; }
  .icon { width: 15px; height: 15px; fill: var(--brand-green); flex: none; }

  .card--one .contacts--phones { left: 46px; top: 124px; }
  .card--one .contacts--web { right: 46px; top: 122px; }
  .card--two .contacts--phones { left: 46px; top: 124px; }
  .card--two .contacts--web { left: 208px; top: 122px; }
  .card--three .contacts--all { left: 46px; top: 88px; }
</style>
</head>
<body>
<svg width="0" height="0" style="position:absolute">
  <defs>
    <symbol id="icon-mobile" viewBox="0 0 16 16"><path d="M4 0h8a1 1 0 0 1 1 1v14a1 1 0 0 1-1 1H4a1 1 0 0 1-1-1V1a1 1 0 0 1 1-1zm1 2v10h6V2zm3 11a1 1 0 1 0 0 2 1 1 0 0 0 0-2z"/></symbol>
    <symbol id="icon-phone" viewBox="0 0 16 16"><path d="M1 5c0-2 3-3 7-3s7 1 7 3v1h-3V4.5H4V6H1zm3 2h8l3 4v4H1v-4zm4 2a2 2 0 1 0 0 4 2 2 0 0 0 0-4z"/></symbol>
    <symbol id="icon-mail" viewBox="0 0 16 16"><path d="M0 3h16v1L8 9 0 4zm0 2.5 8 5 8-5V13H0z"/></symbol>
    <symbol id="icon-globe" viewBox="0 0 16 16"><path d="M8 0a8 8 0 1 0 0 16A8 8 0 0 0 8 0zm0 2a6 6 0 0 1 5.3 3.2L9 9.5 6.5 7 2.3 11.2A6 6 0 0 1 8 2zm1.5 10 4.4-4.4A6 6 0 0 1 7 14z"/></symbol>
  </defs>
</svg>

<section class="card card--one">
  <div class="identity">
    <h1 class="identity__name">GARETH LINDQVIST</h1>
    <p class="identity__title">Operations Manager</p>
  </div>
  <div class="wordmark">HARBORKEY</div>
  <ul class="contacts contacts--phones">
    <li><svg class="icon"><use href="#icon-mobile"/></svg>(555) 384-0651</li>
    <li><svg class="icon"><use href="#icon-phone"/></svg>(555) 384-0649</li>
  </ul>
  <ul class="contacts contacts--web">
    <li><svg class="icon"><use href="#icon-mail"/></svg>Gareth@harborkey-example.ca</li>
    <li><svg class="icon"><use href="#icon-globe"/></svg>www.harborkey-example.ca</li>
  </ul>
</section>

<section class="card card--two">
  <div class="identity">
    <h2 class="identity__name">GARETH LINDQVIST</h2>
    <p class="identity__title">Operations Manager</p>
  </div>
  <div class="wordmark">HARBORKEY</div>
  <ul class="contacts contacts--phones">
    <li><svg class="icon"><use href="#icon-mobile"/></svg>(555) 384-0651</li>
    <li><svg class="icon"><use href="#icon-phone"/></svg>(555) 384-0649</li>
  </ul>
  <ul class="contacts contacts--web">
    <li><svg class="icon"><use href="#icon-mail"/></svg>Gareth@harborkey-example.ca</li>
    <li><svg class="icon"><use href="#icon-globe"/></svg>www.harborkey-example.ca</li>
  </ul>
</section>

<section class="card card--three">
  <div class="identity">
    <h2 class="identity__name">GARETH LINDQVIST</h2>
    <p class="identity__title">Operations Manager</p>
  </div>
  <div class="wordmark">HARBORKEY</div>
  <ul class="contacts contacts--all">
    <li><svg class="icon"><use href="#icon-mobile"/></svg>(555) 384-0651</li>
    <li><svg class="icon"><use href="#icon-phone"/></svg>(555) 384-0649</li>
    <li><svg class="icon"><use href="#icon-mail"/></svg>admin@harborkey-example.ca</li>
    <li><svg class="icon"><use href="#icon-globe"/></svg>www.harborkey-example.ca</li>
  </ul>
</section>
</body>
</html>
```